Business Card: RW Office Partners - Your organised problem solver

Business Name: RW Office Partners
Website: www.rwofficepartners.com.au
Email: marisol@rwofficepartners.com.au
Mobile: 61 482 907 236
Facebook: @rwofficepartners
Instrgram: @rwofficepartners

Brading Colours:
HEX
#986474
#ddccd3
#7a8498
#c9d8e4
#000000
#ffffff

Tag Line: Your organised problem solver

Link to DRAFT website:
https://deskhelpcollective.wixsite.com/rw-office-partners

About Page from the website:
My name is Marisol Wrenfield, and I would love to assist you to become more productive in your day to day and achieve your business and personal goals.
My mission is to give you time, time to work on the important tasks of your business or to be able to spend more time with your family. I will take on the tasks you don’t have time for, don’t know well or simply don’t like to do.
I have an extensive background in Administration, Tender Coordination, Document Control, WHS and Quality Management working primarily in the Construction, Mining and Corporate World.
I am passionate about being organised, having order and making things in your life (and mine) easier! I love to watch something unfold and grow into something amazing! I am known for being the go-to problem solver, the organiser of all things, producing high standards of work even under pressure. I’m also a confident communicator, and I understand that you’re busy running your business.

Target Market(s)

Small to Medium Business who require assistance in their business by a virtual assistant.

Industry/Entity Type

Virtual Assistant

Contact Information for Business Card

Mobile: 61 482 907 236

Font styles to use
Sans Serif

Colors
ffffff

Requirements
Must have
• Branding Colours as outlined.
Contact Details as outlined.
Logo as provided.
Proper contact details - mobile, facebook, instragm, website.
Simple, Elegant, very clean looking.
Should not have
• Note cute with pictures.
Not too girly as still want to market to construction companies.

```html
<!DOCTYPE html>
<html lang="en">
<head>
<meta charset="utf-8">
<title>RW Office Partners – Business Card</title>
<link rel="stylesheet" href="https://fonts.googleapis.com/css2?family=Montserrat:wght@500;600&family=Open+Sans:wght@400&display=swap">
<style>
  :root {
    --mauve: #986474;
    --mauve-soft: #ddccd3;
    --slate: #7a8498;
    --slate-soft: #c9d8e4;
    --ink: #000000;
    --paper: #ffffff;
    --backdrop: #2f2f31;
    --rule: #d9dbe0;
  }
  * { box-sizing: border-box; margin: 0; padding: 0; }
  html, body {
    width: 1200px; height: 866px; overflow: hidden;
    background: var(--backdrop);
  }
  .sheet {
    width: 1200px; height: 866px;
    display: flex; flex-direction: column;
    align-items: center; justify-content: center; gap: 40px;
  }
  .card {
    position: relative;
    width: 640px; height: 366px;
    overflow: hidden;
    box-shadow: 0 8px 22px rgba(0,0,0,.45);
  }

  /* Front */
  .card--front { background: var(--paper); }
  .holder-name {
    position: absolute; left: 44px; top: 84px;
    font: 600 19px/1 "Montserrat", sans-serif;
    color: var(--mauve); text-transform: uppercase; letter-spacing: .02em;
  }
  .contact-list {
    position: absolute; left: 44px; top: 120px;
    list-style: none;
    font: 400 14px/1 "Open Sans", sans-serif; color: var(--ink);
  }
  .contact-list li { display: flex; align-items: center; gap: 10px; height: 24px; }
  .contact-list svg { width: 15px; height: 15px; flex: none; }
  .contact-list .web { color: var(--mauve); }

  .wordmark {
    position: absolute; right: 48px; top: 118px;
    font: 600 34px/1.02 "Montserrat", sans-serif;
    text-transform: uppercase; letter-spacing: .04em; text-align: left;
    color: var(--slate);
  }
  .wordmark--light { color: var(--paper); }

  .divider {
    position: absolute; left: 300px; right: 48px; top: 238px;
    height: 1px; background: var(--rule);
  }
  .social {
    position: absolute; right: 48px; top: 262px;
    display: flex; flex-direction: column; align-items: flex-end; gap: 8px;
  }
  .social-marks { display: flex; gap: 6px; }
  .social-marks span {
    width: 18px; height: 18px; border-radius: 50%;
    border: 1.5px solid var(--slate);
  }
  .social-handle { font: 400 14px/1 "Open Sans", sans-serif; color: var(--ink); }
  .edge-bands { position: absolute; left: 0; bottom: 0; width: 640px; height: 30px; }

  /* Back */
  .card--back { background: var(--slate); }
  .card--back .wordmark { right: auto; left: 210px; top: 120px; font-size: 36px; }
  .tagline {
    position: absolute; left: 150px; top: 232px;
    font: 500 13px/1 "Montserrat", sans-serif;
    color: var(--paper); text-transform: uppercase; letter-spacing: .08em;
  }
</style>
</head>
<body>
<main class="sheet">

  <section class="card card--front" aria-label="Business card front">
    <p class="holder-name">Marisol Wrenfield</p>
    <ul class="contact-list">
      <li>
        <svg viewBox="0 0 16 16" aria-hidden="true"><rect x="1" y="1" width="14" height="14" rx="2" fill="none" stroke="var(--mauve)" stroke-width="1.4"/><path d="M5 4.5c0 4 2.5 6.5 6.5 6.5l.5-1.8-2-1-1 1c-1-.5-1.7-1.2-2.2-2.2l1-1-1-2z" fill="var(--mauve)"/></svg>
        61 482 907 236
      </li>
      <li>
        <svg viewBox="0 0 16 16" aria-hidden="true"><rect x="1" y="3" width="14" height="10" fill="var(--mauve)"/><path d="M1 3l7 5.5L15 3" fill="none" stroke="var(--paper)" stroke-width="1.2"/></svg>
        marisol@rwofficepartners.com.au
      </li>
      <li class="web">
        <svg viewBox="0 0 16 16" aria-hidden="true"><circle cx="8" cy="8" r="6.6" fill="var(--mauve)"/><g fill="none" stroke="var(--paper)" stroke-width=".9"><ellipse cx="8" cy="8" rx="2.8" ry="6.6"/><path d="M1.4 8h13.2M2.5 4.8h11M2.5 11.2h11"/></g></svg>
        www.rwofficepartners.com.au
      </li>
    </ul>

    <h1 class="wordmark">RW Office<br>Partners</h1>
    <div class="divider"></div>

    <div class="social">
      <div class="social-marks" aria-hidden="true"><span></span><span></span></div>
      <p class="social-handle">@rwofficepartners</p>
    </div>

    <svg class="edge-bands" viewBox="0 0 640 30" aria-hidden="true">
      <rect x="0" y="20" width="360" height="10" fill="var(--mauve)"/>
      <polygon points="318,30 340,8 640,8 640,30" fill="var(--slate)"/>
    </svg>
  </section>

  <section class="card card--back" aria-label="Business card back">
    <h2 class="wordmark wordmark--light">RW Office<br>Partners</h2>
    <p class="tagline">Your organised problem solver</p>
  </section>

</main>
</body>
</html>
```